A new presentation to our clients

we are a Real Estate agency, our website is www.lumibrasa.com and it’s time to have a new, fashion and remarcable Business Card. we want to differentiate ourselves from other companies so we want a business card that differentiates us. we want the business card to impact our customers. in the competitive market that we have today, we have to be different and it is this difference that we seek

Target Market(s)

Real Estate Clients

Contact Information for Business Card

We search a totaly diferent card from the usual

Font styles to use
Sans Serif

Colors
e34197

Requirements
Must have
• Logo, adress, phone contact, e-mail, photo, and our website
Nice to have
• We would like to see a modern business card
Should not have
• Houses or building draws

```html
<!DOCTYPE html>
<html lang="en">
<head>
<meta charset="utf-8">
<title>Lumi Brasa – Business Card</title>
<link href="https://fonts.googleapis.com/css2?family=Ubuntu:wght@400;500&display=swap" rel="stylesheet">
<style>
  :root {
    --backdrop: #3a3a3a;
    --brand-pink: #e8267f;
    --brand-pink-light: #ee4a92;
    --paper: #ffffff;
    --ink: #2b2b2b;
    --photo-top: #f0609c;
    --photo-bottom: #7a2a3c;
  }
  * { box-sizing: border-box; margin: 0; padding: 0; }
  html, body { width: 1200px; height: 897px; overflow: hidden; }
  body {
    background: var(--backdrop);
    font-family: "Ubuntu", sans-serif;
    display: flex;
    align-items: center;
    justify-content: center;
    gap: 64px;
  }
  .card {
    width: 440px;
    height: 770px;
    position: relative;
    overflow: hidden;
  }

  /* Contact side */
  .card--contact {
    background: var(--paper);
    color: var(--ink);
    text-align: center;
  }
  .brand-name {
    position: absolute;
    top: 110px; left: 0; right: 0;
    font-size: 54px;
    font-weight: 500;
    color: var(--brand-pink);
    letter-spacing: 1px;
    line-height: 1.2;
  }
  .contact-list {
    position: absolute;
    top: 320px; left: 0; right: 0;
    list-style: none;
  }
  .contact-item { margin-bottom: 30px; }
  .contact-item:last-child { margin-bottom: 0; }
  .contact-icon {
    width: 22px; height: 22px;
    display: block;
    margin: 0 auto 6px;
    fill: var(--brand-pink);
  }
  .contact-rule {
    width: 70px; height: 1px;
    background: var(--ink);
    margin: 0 auto 12px;
  }
  .contact-text { font-size: 19px; letter-spacing: 1px; line-height: 22px; }
  .address {
    position: absolute;
    top: 664px; left: 0; right: 0;
    font-size: 19px;
    line-height: 24px;
    letter-spacing: 0.5px;
  }
  .accent-line {
    position: absolute;
    height: 2px;
    width: 90px;
    background: var(--brand-pink-light);
  }
  .accent-line--top { right: 18px; top: 652px; }
  .accent-line--bottom { left: 28px; top: 738px; }

  /* Portrait side */
  .card--portrait {
    background: linear-gradient(180deg, var(--brand-pink) 0%, var(--brand-pink-light) 60%, var(--brand-pink) 100%);
    color: var(--paper);
    text-align: center;
  }
  .person-name {
    margin-top: 80px;
    font-size: 40px;
    font-weight: 500;
    line-height: 1.2;
  }
  .name-rule {
    width: 250px; height: 1px;
    background: var(--paper);
    margin: 8px auto 8px;
  }
  .person-title { font-size: 20px; letter-spacing: 1px; }
  .portrait-photo {
    position: absolute;
    left: 90px; right: 0; bottom: 0;
    height: 540px;
    border-radius: 140px 140px 0 0;
    background: linear-gradient(180deg, var(--photo-top) 0%, #b54a6a 40%, var(--photo-bottom) 100%);
  }
</style>
</head>
<body>
  <section class="card card--contact">
    <h1 class="brand-name">Lumi Brasa</h1>
    <ul class="contact-list">
      <li class="contact-item">
        <svg class="contact-icon" viewBox="0 0 24 24" aria-hidden="true"><path d="M6.6 10.8a15.1 15.1 0 0 0 6.6 6.6l2.2-2.2a1 1 0 0 1 1-.25 11.4 11.4 0 0 0 3.6.57 1 1 0 0 1 1 1V20a1 1 0 0 1-1 1A17 17 0 0 1 3 4a1 1 0 0 1 1-1h3.5a1 1 0 0 1 1 1c0 1.250.2 2.46.57 3.6a1 1 0 0 1-.25 1z"/></svg>
        <div class="contact-rule"></div>
        <p class="contact-text">123 555 0148</p>
      </li>
      <li class="contact-item">
        <svg class="contact-icon" viewBox="0 0 24 24" aria-hidden="true"><path d="M2 5h20v14H2z" fill="var(--brand-pink)"/><path d="M2 6l10 7.5L22 6" fill="none" stroke="#fff" stroke-width="1.6"/></svg>
        <div class="contact-rule"></div>
        <p class="contact-text">info@lumibrasa.com</p>
      </li>
      <li class="contact-item">
        <svg class="contact-icon" viewBox="0 0 24 24" aria-hidden="true"><g fill="none" stroke="var(--brand-pink)" stroke-width="1.8"><circle cx="12" cy="12" r="9.5"/><ellipse cx="12" cy="12" rx="4" ry="9.5"/><path d="M2.5 12h19M4 7h16M4 17h16"/></g></svg>
        <div class="contact-rule"></div>
        <p class="contact-text">www.lumibrasa.com</p>
      </li>
    </ul>
    <div class="accent-line accent-line--top"></div>
    <p class="address">48 Corran Lane, Suite B<br>Leeds, UK L0034C</p>
    <div class="accent-line accent-line--bottom"></div>
  </section>

  <section class="card card--portrait">
    <h2 class="person-name">Elias Marrow</h2>
    <div class="name-rule"></div>
    <p class="person-title">Managing Partner</p>
    <div class="portrait-photo" role="img" aria-label="Portrait photo of the managing partner in a red checked shirt"></div>
  </section>
</body>
</html>
```